ORLA - Óptica Médica - web design and concept

Website concept - Create and develop our website design and structure. ORLA is an optical store chain, and we are looking to establish our web and digital concept. In attachment there are several pictures about our stores and our logo.

The website structure should be user friendly. Colors should be light and the design as simple and minimalist as possible. There are different variations of the logothat can be used, check the file.

The website will include optical collections and sun collections as an online store. Also, a medical menu should be considered in order for clients to schedule optometry appointments. There should also be a menu for client assistance where the clients can read about glass maintenance in our workshop.
Updates

Low design quality

Number of Pages Required

5+ page

Font styles to use
Serif
Sans Serif

Requirements
Must have
• Must be user-friendly and minimalist.
• Please USE PICTURES FROM THE BRANDS we sell: MERUN, BOSKA, PNW, KOLE, BAMPE
Nice to have
• Nice to inspire: ZEK glasses (see website https://ch.shopzek.com/en/)
• Nice to inspire: https://merun-eyewear.com/
• Nice to ispire: https://www.pnwglobe.com/en/
Should not have
• Hysteric colors and shapes

```html
<!DOCTYPE html>
<html lang="en">
<head>
<meta charset="utf-8">
<title>ORLA Óptica Médica – Contact</title>
<link href="https://fonts.googleapis.com/css2?family=Raleway:wght@400;600;700&family=Playfair+Display:wght@400&display=swap" rel="stylesheet">
<style>
:root{
  --ink:#222;
  --muted:#777;
  --line:#d8d8d8;
  --panel:#eeeeee;
  --hero-a:#f4f4f4;
  --hero-b:#e6e6e6;
  --footer:#2b2b2b;
  --footer-deep:#1d1d1d;
  --footer-text:#cfcfcf;
  --white:#fff;
  --black:#111;
}
*{margin:0;padding:0;box-sizing:border-box}
html,body{width:826px;height:1200px;overflow:hidden;background:var(--white)}
body{font-family:'Raleway',Arial,sans-serif;color:var(--ink);position:relative}

.site-header{position:absolute;top:0;left:0;width:826px;height:105px;background:var(--white)}
.header-phone{position:absolute;left:88px;top:52px;font-size:11px;color:var(--muted);display:flex;align-items:center;gap:8px}
.brand-logo{position:absolute;left:0;width:826px;top:22px;text-align:center}
.brand-logo .mark{font-family:'Playfair Display',Georgia,serif;font-size:26px;letter-spacing:6px;color:var(--ink)}
.brand-logo .tag{font-size:7px;letter-spacing:3px;color:var(--muted);margin-top:2px}
.header-icons{position:absolute;right:86px;top:50px;display:flex;gap:14px}

.hero{position:absolute;top:105px;left:0;width:826px;height:250px;background:linear-gradient(90deg,var(--hero-a),var(--hero-b))}
.hero h1{position:absolute;left:110px;top:100px;font-weight:400;font-size:30px;color:var(--ink)}
.hero-photo{position:absolute;left:455px;top:0;width:210px;height:250px;background:linear-gradient(180deg,#d9cbc2,#b9a79e 60%,#9a9a9a)}

.contact-panel{position:absolute;left:80px;top:390px;width:665px;height:315px;background:var(--panel)}
.quick-form{position:absolute;left:25px;top:30px;width:270px}
.quick-form h2{font-size:26px;font-weight:600;letter-spacing:1px;margin-bottom:18px}
.field{height:27px;border-bottom:1px solid var(--line);font-size:10px;color:#999;padding:8px 0 0 2px;margin-bottom:8px;background:var(--panel)}
.field.message{height:48px}
.send-btn{margin-top:20px;height:28px;background:var(--black);color:var(--white);font-size:10px;font-weight:700;letter-spacing:1px;display:flex;align-items:center;justify-content:center}
.map{position:absolute;left:330px;top:6px;width:328px;height:303px;background:linear-gradient(135deg,#e8e8e8,#d6d6d6)}

.brands{position:absolute;top:810px;left:0;width:826px}
.brands h3{text-align:center;font-weight:400;font-size:16px;margin-bottom:24px}
.brand-row{position:relative;display:flex;justify-content:center;gap:18px}
.brand-tile{width:95px;height:48px;border:1px solid #eee;box-shadow:0 1px 3px rgba(0,0,0,.08);display:flex;align-items:center;justify-content:center;font-size:13px;font-weight:600;color:var(--ink);white-space:nowrap}
.arrow{position:absolute;top:12px;width:22px;height:22px;border-radius:50%;background:#222}
.arrow.prev{left:36px}.arrow.next{right:36px}

.site-footer{position:absolute;top:955px;left:0;width:826px;height:245px;background:var(--footer);color:var(--footer-text);font-size:9px}
.footer-about{position:absolute;left:82px;top:22px;width:170px}
.footer-about .mark{font-family:'Playfair Display',Georgia,serif;font-size:20px;letter-spacing:5px;color:var(--white)}
.footer-about .tag{font-size:6px;letter-spacing:2px;margin-bottom:12px}
.footer-about p{line-height:1.4;margin-bottom:6px}
.footer-about li{list-style:none;line-height:1.6}
.pay-row{display:flex;gap:4px;margin-top:8px}
.pay-card{width:28px;height:14px;background:#eaeaea;color:#333;font-size:6px;font-weight:700;display:flex;align-items:center;justify-content:center}
.footer-col{position:absolute;top:48px}
.footer-col h4{font-size:8px;font-weight:700;color:var(--white);letter-spacing:1px;margin-bottom:12px}
.info{left:285px}
.info li{list-style:none;line-height:1.75}
.info li::before{content:'';display:inline-block;width:4px;height:4px;border-radius:50%;background:var(--footer-text);margin-right:8px;vertical-align:middle}
.tags{left:410px;width:140px}
.tag-grid{display:grid;grid-template-columns:repeat(3,40px);gap:6px}
.tag-grid span{border:1px solid #666;height:16px;display:flex;align-items:center;justify-content:center;font-size:7px}
.insta{left:580px}
.insta-grid{display:grid;grid-template-columns:repeat(4,28px);gap:4px}
.insta-grid span{height:28px;background:linear-gradient(135deg,#8f8f8f,#5d5d5d)}
.footer-bar{position:absolute;bottom:0;left:0;width:826px;height:30px;background:var(--footer-deep);display:flex;align-items:center;padding:0 82px;justify-content:space-between;font-size:8px}
.social{display:flex;gap:6px}
.social span{width:14px;height:14px;border-radius:50%;background:#ddd}
</style>
</head>
<body>

<header class="site-header">
  <div class="header-phone">
    <svg width="12" height="12" viewBox="0 0 24 24"><circle cx="12" cy="12" r="11" fill="none" stroke="#777" stroke-width="1.5"/><path d="M8 7c0 5 4 9 9 9l1-2-3-1-1 1c-2-1-3-2-4-4l1-1-1-3z" fill="#777"/></svg>
    123-456-7890
  </div>
  <div class="brand-logo">
    <div class="mark">ORLA</div>
    <div class="tag">ÓPTICA MÉDICA</div>
  </div>
  <div class="header-icons">
    <svg width="10" height="10" viewBox="0 0 10 10"><circle cx="5" cy="3" r="2.2" fill="none" stroke="#333"/><path d="M1 10c0-3 8-3 8 0" fill="none" stroke="#333"/></svg>
    <svg width="10" height="10" viewBox="0 0 10 10"><path d="M1 2h8l-1 5H2z" fill="none" stroke="#333"/><circle cx="3" cy="9" r=".8" fill="#333"/><circle cx="7" cy="9" r=".8" fill="#333"/></svg>
    <svg width="10" height="10" viewBox="0 0 10 10"><circle cx="4" cy="4" r="3" fill="none" stroke="#333"/><path d="M6.2 6.2 9 9" stroke="#333"/></svg>
    <svg width="10" height="10" viewBox="0 0 10 10"><path d="M1 2h8M1 5h8M1 8h8" stroke="#333"/></svg>
  </div>
</header>

<section class="hero">
  <h1>Contact us</h1>
  <div class="hero-photo" role="img" aria-label="Smiling woman wearing red eyeglasses"></div>
</section>

<section class="contact-panel">
  <form class="quick-form">
    <h2>QuicK Contact</h2>
    <div class="field">Name</div>
    <div class="field">Phone</div>
    <div class="field">E-Mail</div>
    <div class="field message">Message</div>
    <div class="send-btn">SEND MESSAGE</div>
  </form>
  <div class="map" role="img" aria-label="Street map showing the store location">
    <svg style="position:absolute;left:150px;top:110px" width="22" height="30" viewBox="0 0 22 30"><path d="M11 0C5 0 0 5 0 11c0 8 11 19 11 19s11-11 11-19C22 5 17 0 11 0z" fill="#111"/><circle cx="11" cy="11" r="4" fill="#ddd"/></svg>
  </div>
</section>

<section class="brands">
  <h3>Brands</h3>
  <div class="brand-row">
    <span class="arrow prev"><svg width="22" height="22"><path d="M13 6 8 11l5 5" fill="none" stroke="#fff" stroke-width="2"/></svg></span>
    <div class="brand-tile">Solenne</div>
    <div class="brand-tile">Aerith Paris</div>
    <div class="brand-tile">mara quill</div>
    <div class="brand-tile">Velmont</div>
    <div class="brand-tile">Tovik Eyewear</div>
    <span class="arrow next"><svg width="22" height="22"><path d="M9 6l5 5-5 5" fill="none" stroke="#fff" stroke-width="2"/></svg></span>
  </div>
</section>

<footer class="site-footer">
  <div class="footer-about">
    <div class="mark">ORLA</div>
    <div class="tag">ÓPTICA MÉDICA</div>
    <p>Lorem Ipsum is simply dummy text ipsum is simply the dummy text of print.</p>
    <ul>
      <li>Phone: 123 456 7890</li>
      <li>Email@info.com</li>
      <li>Address - 12th Street, City, Usa</li>
    </ul>
    <div class="pay-row">
      <span class="pay-card">Payo</span><span class="pay-card">Carda</span><span class="pay-card">Mondo</span><span class="pay-card">Lumo</span>
    </div>
  </div>
  <div class="footer-col info">
    <h4>INFORMATION</h4>
    <ul><li>Home</li><li>Women</li><li>Men</li><li>Kids</li><li>Testimonials</li><li>Blogs</li><li>Contact Us</li></ul>
  </div>
  <div class="footer-col tags">
    <h4>POPULAR TAGS</h4>
    <div class="tag-grid">
      <span>Sale</span><span>Men</span><span>Lady</span>
      <span>Women</span><span>Latest</span><span>Specials</span>
      <span>Fashion</span><span>Eye</span><span>offers</span>
      <span>Frames</span><span>COOL</span>
    </div>
  </div>
  <div class="footer-col insta">
    <h4>INSTAGRAM</h4>
    <div class="insta-grid" role="img" aria-label="Grid of customer photos wearing eyewear">
      <span></span><span></span><span></span><span></span>
      <span></span><span></span><span></span><span></span>
    </div>
  </div>
  <div class="footer-bar">
    <span>Copyright © 2018 Orla Óptica Médica. All Right Reserve</span>
    <div class="social"><span></span><span></span><span></span><span></span><span></span></div>
  </div>
</footer>

</body>
</html>
```